Schlichtes Design für Malerbetrieb
Zielgruppe
Wir sind ein mittelgroßer Malerbetrieb in München mit umfangreichem Leistungsspektrum.
Unsere Hauptleistungen sind: Fassadenrenovierung, Altbausanierung, Betoninstandsetzung, Balkonabdichtung (kein Neubau!).
Unsere Zielgruppen sind: Hausverwaltungen, Firmen und Privatpersonen.
Unsere Kunden schätzen: Konstruktive Organisation und Planung im Vorfeld, Zuverlässigkeit, saubere Arbeitsweise, dauerhafte Balkonabdichtungen.
Aufgabenstellung
Wir möchten eine langlebige, stilvolle, minimalistische Homepage.
Wir möchten von der bestehenden Homepage nur die Schriftart für unseren Firmennamen (Century Gothic) und wenn möglich (nicht zwingend), irgendwo das florale Muster einbauen. Corporate-Design haben wir nicht.
Farbtöne: Firmennamen Orange (hellorange bis erdiges Orange möglich, da sind wir nicht fixiert) , einen dunklen Hintergrundfarbton (Petrol-Blaugrau ?) mit gelbem (neon bis senfgelb) Akzent (Linien), Blumenmuster weiß, grau.
Dies sind nur unsere Ideen. Wir sind aber auch absolut offen für eure Profi-Ideen.
Wir möchten uns von den unzähligen langweiligen 'Pinselseiten mit veralteten Bilder' unserer Kollegen interessant und mit Stil abheben.
Eher nach dem Motto 'weniger ist mehr'.
Einen positiven, sympathischen Eindruck geben und unsere Leistungen in den Vordergrund bringen.
Da wir viele Stammkunden haben, betreiben wir kein Social-Media und möchten dies vorerst auch nicht tun.
Die Seite wird in den nächsten Jahren nicht verändert, höchstens die Bilder aktualisiert.
Die Texte haben wir alle selbst entworfen und möchten wir so übernehmen.
Die Galerien sollen unkompliziert anzuschauen sein.
Uns gefällt die Struktur und Schlichtheit von https://vaartmolen.nl/ oder Timbra.de gut und wir mögen Vintage-Grafiken gerne.
Einerseits darf die Seite geradlinig, andererseits aber auch rund und floral wirken.

```html
<!DOCTYPE html>
<html lang="de">
<head>
<meta charset="utf-8">
<title>kolbrit – Malerarbeiten</title>
<link rel="stylesheet" href="https://fonts.googleapis.com/css2?family=Questrial&family=Oswald:wght@300&family=Arimo:wght@400&display=swap">
<style>
  :root {
    --charcoal: #3e3e40;
    --charcoal-light: #474749;
    --navy: #333253;
    --orange: #f5a829;
    --white: #ffffff;
  }
  html, body {
    margin: 0;
    width: 1200px;
    height: 900px;
    overflow: hidden;
    background: var(--charcoal);
  }
  .page {
    position: relative;
    width: 1200px;
    height: 900px;
    background: var(--charcoal-light);
    font-family: "Arimo", Arial, sans-serif;
    color: var(--white);
  }
  .site-header {
    position: absolute;
    inset: 0 0 auto 0;
    height: 125px;
    background: var(--charcoal);
  }
  .brand {
    position: absolute;
    right: 28px;
    top: 12px;
    margin: 0;
    font-family: "Questrial", "Century Gothic", sans-serif;
    font-weight: 400;
    font-size: 54px;
    letter-spacing: 1px;
    color: var(--orange);
  }
  .main-nav {
    position: absolute;
    right: 25px;
    top: 81px;
    display: flex;
    gap: 18px;
  }
  .main-nav a, .footer-nav a {
    font-family: "Oswald", sans-serif;
    font-weight: 300;
    text-transform: uppercase;
    text-decoration: none;
    color: var(--white);
  }
  .main-nav a { font-size: 23px; letter-spacing: 0.3px; }
  .main-nav a.is-active { color: var(--orange); }
  .ornament-band {
    position: absolute;
    left: 0; top: 125px;
    width: 1200px; height: 338px;
    background: linear-gradient(180deg, #4a4a4c 0%, #434345 100%);
  }
  .stage {
    position: absolute;
    left: 0; top: 0;
  }
  .gallery-photo {
    position: absolute;
    top: 200px;
    height: 261px;
  }
  .photo-1 { left: 0; width: 444px; background: linear-gradient(180deg, #a9b7c8 0%, #cfc9c0 45%, #8f8b7f 100%); }
  .photo-2 { left: 468px; width: 288px; background: linear-gradient(90deg, #d9b583 0%, #c9a06c 60%, #a8c8e6 100%); }
  .photo-3 { left: 778px; width: 422px; background: linear-gradient(180deg, #c7c8ca 0%, #b4b5b8 60%, #8e8f92 100%); }
  .gallery-arrow {
    position: absolute;
    top: 474px;
  }
  .arrow-prev { left: 12px; }
  .arrow-next { right: 12px; }
  .copy {
    position: absolute;
    top: 539px;
    margin: 0;
    font-size: 13px;
    line-height: 20.6px;
  }
  .copy p { margin: 0 0 20.6px; }
  .copy-left { left: 67px; width: 500px; }
  .copy-right { left: 620px; width: 520px; }
  .site-footer {
    position: absolute;
    left: 0; bottom: 0;
    width: 1200px; height: 63px;
    background: var(--charcoal);
  }
  .footer-nav {
    position: absolute;
    right: 32px;
    top: 12px;
    display: flex;
    gap: 17px;
  }
  .footer-nav a { font-size: 24px; font-weight: 400; }
</style>
</head>
<body>
<div class="page">
  <header class="site-header">
    <h1 class="brand">kolbrit</h1>
    <nav class="main-nav">
      <a class="is-active" href="#">Malerarbeiten</a>
      <a href="#">Betoninstandsetzung</a>
      <a href="#">Balkonabdichtung</a>
      <a href="#">Farbgestaltung</a>
      <a href="#">Wärmedämmung</a>
      <a href="#">Ausbildung</a>
      <a href="#">Portrait</a>
    </nav>
  </header>

  <div class="ornament-band" role="img" aria-label="Florales Muster in Grau auf dunklem Grund"></div>

  <svg class="stage" width="1200" height="900" viewBox="0 0 1200 900" aria-hidden="true">
    <polygon points="0,462 444,462 1200,836 0,836" fill="var(--navy)"/>
  </svg>

  <div class="gallery-photo photo-1" role="img" aria-label="Foto: sanierte Altbaufassade mit Erkern und Bäumen"></div>
  <div class="gallery-photo photo-2" role="img" aria-label="Foto: ockerfarbener Erker mit Stuckverzierung"></div>
  <div class="gallery-photo photo-3" role="img" aria-label="Foto: graue Fassade mit Balkonen"></div>

  <svg class="gallery-arrow arrow-prev" width="26" height="22" viewBox="0 0 26 22" aria-label="Zurück" role="img">
    <path d="M24 11H4M12 3L4 11l8 8" fill="none" stroke="var(--orange)" stroke-width="3"/>
  </svg>
  <svg class="gallery-arrow arrow-next" width="26" height="22" viewBox="0 0 26 22" aria-label="Weiter" role="img">
    <path d="M2 11h20M14 3l8 8-8 8" fill="none" stroke="var(--orange)" stroke-width="3"/>
  </svg>

  <div class="copy copy-left">
    <p>Flächen, die einheitlich und streifenlos erscheinen, erfreuen den Betrachter.<br>
    Sie unterstützen primär die optische Erscheinung eines Objekts.<br>
    Auf längere Zeit gesehen leisten Anstriche jedoch weitere wesentliche Dienste.<br>
    Sie schützen Ihr Gebäude oder Ihre Wohnung vor Witterungseinflüssen,<br>
    mechanischer Beschädigung und dem Nagen der Zeit. Unsere Tätigkeit<br>
    und unser Fachwissen schützen Ihren Besitz.</p>
    <p>Bei der Erstellung von baulichen Schutzmaßnahmen müssen alle Objekt-<br>
    gegebenheiten mit einbezogen werden. Um einen dauerhaften Bestand von<br>
    Objekten zu gewährleisten, muss jeder Beteiligte über das eigene<br>
    Aufgabengebiet hinweg denken.</p>
  </div>

  <div class="copy copy-right">
    <p>Wir betrachten bei der Ausarbeitung unserer Leistungen jedes Bauteil<br>
    gesondert mit seinen Eigenschaften. Die stets erneuerten Technologien<br>
    von Anstrichmitteln in Bezug auf Oberflächenbeschaffenheit,<br>
    Umweltverträglichkeit und Beständigkeit setzen wir jederzeit optimal ein.<br>
    Nur Fachleute suchen nach Ursachen und erarbeiten die richtigen Lösungen.</p>
  </div>

  <footer class="site-footer">
    <nav class="footer-nav">
      <a href="#">Kontakt</a>
      <a href="#">Impressum</a>
      <a href="#">Datenschutz</a>
    </nav>
  </footer>
</div>
</body>
</html>
```